Tech business card design

We need an amazing business card design for our new business 'Pexla' a marketing tech startup based in Sydney, Australia. We provide an online marketplace for businesses to search and buy advertising media, connect with service providers and learn more about marketing. We wish to communicate 'cool tech', reliability and professionalism and design based around our logo.

Target Market(s)

Business Owners

Contact Information for Business Card

Name
Position
Email Address
Website
Phone Number

Font styles to use
Other font styles liked:
• Avenir & Avenir Next

Colors

Designer to choose colors to be used in the design.

```html
<!DOCTYPE html>
<html lang="en">
<head>
<meta charset="utf-8">
<title>Pexla Business Card</title>
<link href="https://fonts.googleapis.com/css2?family=Nunito+Sans:wght@400;700;800&display=swap" rel="stylesheet">
<style>
  :root {
    --page-bg: #e1dddd;
    --navy: #12133a;
    --slate: #82869a;
    --sheen: #e6e6f2;
    --white: #ffffff;
    --muted: #c9cae0;
  }
  * { margin: 0; padding: 0; box-sizing: border-box; }
  html, body {
    width: 975px; height: 1200px; overflow: hidden;
    background: var(--page-bg);
    font-family: "Nunito Sans", "Avenir Next", Avenir, sans-serif;
  }
  .canvas { position: relative; width: 975px; height: 1200px; }
  .card {
    position: absolute; width: 863px; height: 495px;
    border-radius: 34px; overflow: hidden; background: var(--navy);
  }
  .card--front { left: 57px; top: 70px; }
  .card--back { left: 66px; top: 627px; }
  .card__bands { position: absolute; inset: 0; }
  .brand-name {
    position: absolute; color: var(--white); font-weight: 800;
    letter-spacing: -2px; line-height: 1;
  }
  .card--front .brand-name { left: 42px; top: 222px; font-size: 118px; }
  .card--back .brand-name {
    left: 0; right: 0; top: 342px; text-align: center; font-size: 150px;
    transform: translateY(-50%);
  }
  .contact {
    position: absolute; right: 65px; top: 160px; text-align: right; color: var(--white);
  }
  .contact__name { font-weight: 700; font-size: 27px; letter-spacing: 0.3px; line-height: 1.2; }
  .contact__role { font-size: 24px; color: var(--muted); line-height: 1.2; margin-bottom: 18px; }
  .contact__line {
    display: flex; justify-content: flex-end; align-items: center; gap: 6px;
    font-size: 20px; line-height: 33px;
  }
  .contact__line svg { width: 22px; height: 22px; flex: none; }
  .contact__address { font-size: 21px; line-height: 29px; margin-top: 14px; }
  .card__url {
    position: absolute; left: 0; right: 0; top: 400px; text-align: center;
    color: var(--white); font-size: 26px; letter-spacing: 3px;
  }
</style>
</head>
<body>
<main class="canvas">
  <section class="card card--front">
    <svg class="card__bands" viewBox="0 0 863 495" aria-hidden="true">
      <rect width="863" height="495" fill="var(--navy)"/>
      <polygon points="0,0 571,0 332,495 0,495" fill="var(--slate)"/>
      <polygon points="526,0 562,0 378,420 364,424" fill="var(--sheen)"/>
    </svg>
    <div class="brand-name">Pexla</div>
    <div class="contact">
      <div class="contact__name">JOHN SMITH</div>
      <div class="contact__role">Position</div>
      <div class="contact__line">012-345-6789
        <svg viewBox="0 0 24 24" fill="none" stroke="#fff" stroke-width="2">
          <circle cx="12" cy="12" r="10"/>
          <path d="M8 6.5l2 2.5-1.2 1.5c.8 1.8 2 3 3.8 3.8l1.5-1.2 2.5 2-1.3 1.8c-4.5-.5-8.3-4.3-8.8-8.8z" fill="#fff" stroke-width="1"/>
        </svg>
      </div>
      <div class="contact__line">info@pexla.com
        <svg viewBox="0 0 24 24"><rect x="2" y="5" width="20" height="14" fill="#fff"/><path d="M2 5l10 8 10-8M2 19l8-7M22 19l-8-7" stroke="var(--navy)" stroke-width="1.6" fill="none"/></svg>
      </div>
      <div class="contact__line">www.pexla.com
        <svg viewBox="0 0 24 24" fill="none" stroke="#fff" stroke-width="1.6">
          <circle cx="12" cy="12" r="10"/><ellipse cx="12" cy="12" rx="4.5" ry="10"/>
          <path d="M2 12h20M4 7h16M4 17h16M12 2v20"/>
        </svg>
      </div>
      <div class="contact__address">Street name City Name,<br>Zipcode,012345</div>
    </div>
  </section>

  <section class="card card--back">
    <div class="brand-name">Pexla</div>
    <div class="card__url">www.pexla.com</div>
  </section>
</main>
</body>
</html>
```